KRT,LLC

I need a flyer that has my company Logo on it as well as my book cover on it. I need for the flyer to read: "Rust on the harbor gate" ~ A story of Money,Murder,Sex and family ties in the heart of the city. Read along as Desmond L. Ferris masterfully paint this Wilmington,Delaware tale like no other~The "K.T.Z crew" clash in a rain of bullets against North sides own "Pinto crew."
At $14.99 you can own your own copy of "Rust on the harbor gate."
Contact Des Ferris @ 302-555-0147 to purchase your paper back copy.
OR
Visit:www.krtllcbooks-example.com
www.rustontheharborgate-example.com
rustharborgate24@example.net
To purchase your order directly off line.
We accept paxo,TellarPay and debit cards for those individuals who wish to order on-line!

```html
<!DOCTYPE html>
<html lang="en">
<head>
<meta charset="utf-8">
<title>Rust on the Harbor Gate – Flyer</title>
<link rel="stylesheet" href="https://fonts.googleapis.com/css2?family=Alfa+Slab+One&family=Creepster&family=Open+Sans:wght@400;700;800&display=swap">
<style>
  :root {
    --backdrop: #7a1216;
    --paper: #ffffff;
    --blood: #8e1a1d;
    --title-red: #a0151b;
    --title-blue: #2d47a8;
    --accent-red: #e0262c;
    --ink: #1c1c1c;
    --gold: #f2c21b;
    --band: #8c1419;
    --black: #080808;
    --cover-blue: #2a3596;
  }
  * { box-sizing: border-box; margin: 0; padding: 0; }
  html, body { width: 1200px; height: 1000px; overflow: hidden; }
  body { background: var(--backdrop); font-family: "Open Sans", Arial, sans-serif; position: relative; }

  .flyer {
    position: absolute; left: 160px; top: 30px; width: 880px; height: 940px;
    background: var(--paper); overflow: hidden;
  }
  .flyer > * { position: absolute; }

  .collage {
    left: 0; top: 330px; width: 880px; height: 520px;
    background:
      radial-gradient(ellipse at 18% 55%, rgba(150,110,95,.75), transparent 60%),
      radial-gradient(ellipse at 82% 45%, rgba(95,100,95,.8), transparent 60%),
      linear-gradient(180deg, rgba(255,255,255,1) 0%, rgba(205,200,198,.7) 25%, rgba(170,160,158,.8) 60%, rgba(240,240,240,.9) 100%);
  }

  .title-main {
    left: 0; width: 100%; top: 40px; text-align: center;
    font-family: "Creepster", "Alfa Slab One", cursive;
    font-size: 138px; line-height: 1; color: var(--blood); letter-spacing: 4px;
  }
  .title-sub {
    left: 0; width: 100%; top: 190px; text-align: center;
    font-family: "Alfa Slab One", Georgia, serif; font-size: 40px; color: var(--title-red); letter-spacing: 1px;
  }
  .title-sub .last { color: var(--title-blue); }

  .tagline { left: 0; width: 100%; text-align: center; color: var(--ink); }
  .tagline.lead { top: 250px; font-size: 22px; }
  .tagline.lead strong { color: var(--accent-red); font-weight: 700; }
  .tagline.body { top: 284px; font-size: 16px; line-height: 1.35; padding: 0 80px; }
  .tagline.quote { top: 336px; font-size: 24px; line-height: 32px; }

  .book-cover {
    left: 167px; top: 400px; width: 356px; height: 250px;
    background: linear-gradient(90deg, var(--cover-blue) 0%, #3240a6 48%, #1f2a80 50%, var(--cover-blue) 100%);
    box-shadow: 0 4px 10px rgba(0,0,0,.4);
  }
  .badge { left: 470px; top: 372px; width: 130px; height: 130px; }

  .price-line { left: 0; width: 100%; top: 698px; text-align: center; font-size: 20px; line-height: 30px; color: var(--ink); }
  .price-line b { font-size: 26px; font-weight: 800; }
  .title-repeat {
    left: 0; width: 100%; top: 728px; text-align: center;
    font-size: 30px; line-height: 40px; font-weight: 800; color: var(--accent-red);
  }
  .contact-band {
    left: 140px; top: 770px; width: 600px; height: 48px;
    background: var(--band); border-radius: 6px;
  }
  .contact-line {
    left: 0; width: 100%; top: 772px; text-align: center;
    font-size: 30px; line-height: 44px; font-weight: 700; color: var(--gold);
    text-shadow: 0 2px 3px rgba(0,0,0,.6);
  }
  .contact-line b { font-weight: 800; }

  .footer-shape { left: 0; top: 820px; width: 880px; height: 90px; }
  .purchase-note { left: 0; width: 100%; top: 826px; text-align: center; font-size: 16px; line-height: 22px; color: var(--ink); }
  .or-note { left: 0; width: 100%; top: 852px; text-align: center; font-size: 14px; line-height: 18px; color: var(--paper); }

  .brand {
    left: 22px; top: 818px; width: 88px; height: 88px; border-radius: 50%;
    background: var(--black); border: 3px solid var(--paper);
    display: flex; align-items: center; justify-content: center;
    color: var(--paper); font-weight: 800; font-size: 14px;
  }
  .links { top: 870px; left: 0; width: 100%; height: 19px; font-size: 14px; line-height: 19px; font-weight: 700; color: var(--gold); }
  .links span { position: absolute; }
  .links .site-a { left: 128px; }
  .links .site-b { left: 475px; }
  .offline { left: 0; width: 100%; top: 890px; text-align: center; font-size: 13px; line-height: 18px; color: var(--paper); }

  .payment-strip {
    left: 0; top: 910px; width: 880px; height: 30px; background: var(--band);
    color: var(--paper); font-size: 14px; text-align: center; line-height: 30px;
  }
</style>
</head>
<body>
  <main class="flyer">
    <div class="collage" role="img" aria-label="Collage of street photos: characters from the story, city corners, a stack of cash and a street sign"></div>

    <h1 class="title-main">RUST ON</h1>
    <h2 class="title-sub">THE HARBOR <span class="last">GATE</span></h2>

    <p class="tagline lead">A story of <strong>Money, Murder, Sex and family</strong> ties in the heart of the city.</p>
    <p class="tagline body">Read along as Desmond L. Ferris masterfully paint this Wilmington, Delaware tale like no other~The "K.T.Z crew" clash in a rain of bullets against North sides own</p>
    <p class="tagline quote">"Pinto crew."</p>

    <div class="book-cover" role="img" aria-label="Book cover of Rust on the harbor gate, front and back spread in blue"></div>

    <svg class="badge" viewBox="0 0 150 150" aria-label="Buy $14.99 only">
      <polygon fill="#ffd21a" stroke="#f0a010" stroke-width="2"
        points="75,4 86,22 105,10 108,32 130,28 123,49 144,57 127,71 142,88 121,94 128,116 106,114 102,136 84,124 75,146 66,124 48,136 44,114 22,116 29,94 8,88 23,71 6,57 27,49 20,28 42,32 45,10 64,22"/>
      <text x="75" y="58" text-anchor="middle" font-family="Open Sans, Arial, sans-serif" font-weight="700" font-size="26" fill="#d41f26">Buy</text>
      <text x="75" y="88" text-anchor="middle" font-family="Open Sans, Arial, sans-serif" font-weight="800" font-size="26" fill="#d41f26">$14.99</text>
      <text x="75" y="110" text-anchor="middle" font-family="Open Sans, Arial, sans-serif" font-weight="700" font-size="17" fill="#d41f26">Only</text>
    </svg>

    <p class="price-line">At <b>$14.99</b> you can own your own copy of</p>
    <p class="title-repeat">"Rust on the harbor gate."</p>
    <div class="contact-band"></div>
    <p class="contact-line">Contact Des Ferris @ <b>302-555-0147</b></p>

    <svg class="footer-shape" viewBox="0 0 880 90" preserveAspectRatio="none" aria-hidden="true">
      <path d="M0,0 C250,45 630,45 880,0 L880,90 L0,90 Z" fill="#080808"/>
    </svg>
    <p class="purchase-note">to purchase your paper back copy.</p>
    <p class="or-note">OR</p>

    <div class="brand">KRT,LLC</div>

    <p class="links">
      <span class="site-a">Visit: www.krtllcbooks-example.com</span>
      <span class="site-b">www.rustontheharborgate-example.com</span>
    </p>
    <p class="offline">To purchase your order directly off line.</p>

    <p class="payment-strip">We accept paxo, TellarPay and debit cards for those individuals who wish to order on-line!</p>
  </main>
</body>
</html>
```